Corporate Business Card

Very professional, Modern, Not to busy, include phone address email, website
(253) 617-4930, 18761 52nd Avenue S, Kent, WA 98047, martin@plumlinegroup.com, varkoworks.com

Target Market(s)

Manufacturing

Industry/Entity Type

Aero, machining, manufacturing, Off road racing

Contact Information for Business Card

Phone, address email, website

```html
<!DOCTYPE html>
<html lang="en">
<head>
<meta charset="utf-8">
<title>Varko Works – Business Card</title>
<link href="https://fonts.googleapis.com/css2?family=Roboto:wght@400;500;700&family=Rajdhani:wght@700&display=swap" rel="stylesheet">
<style>
  :root {
    --stage: #2b2b2d;
    --navy: #2b3a6b;
    --navy-deep: #24315c;
    --red: #c02026;
    --white: #f2f3f6;
    --soft: #d9dce6;
  }
  html, body {
    margin: 0;
    padding: 0;
    width: 1200px;
    height: 1138px;
    overflow: hidden;
    background: var(--stage);
    font-family: "Roboto", Arial, sans-serif;
  }
  .card {
    position: absolute;
    left: 275px;
    width: 620px;
    height: 375px;
    border-radius: 16px;
    background: linear-gradient(180deg, var(--navy) 0%, var(--navy-deep) 100%);
    overflow: hidden;
  }
  .card--front { top: 186px; }
  .card--back { top: 608px; }

  .brand-name {
    position: absolute;
    left: 0;
    right: 0;
    top: 128px;
    text-align: center;
    font-weight: 700;
    font-size: 62px;
    letter-spacing: 3px;
    color: var(--soft);
    margin: 0;
  }
  .front-web {
    position: absolute;
    left: 0;
    right: 0;
    top: 326px;
    text-align: center;
    font-size: 16px;
    letter-spacing: 11px;
    color: var(--white);
  }
  .front-web .accent { color: var(--red); }

  .holder-name {
    position: absolute;
    left: 26px;
    top: 74px;
    margin: 0;
    font-family: "Rajdhani", "Roboto", sans-serif;
    font-weight: 700;
    font-size: 29px;
    letter-spacing: 0.5px;
    color: var(--white);
  }
  .holder-name .surname { color: var(--red); }

  .contact-band {
    position: absolute;
    left: 0;
    top: 138px;
    width: 302px;
    height: 98px;
    background: var(--red);
  }
  .contact-list {
    list-style: none;
    margin: 0;
    padding: 13px 0 0 26px;
  }
  .contact-list li {
    display: flex;
    align-items: center;
    height: 24.5px;
    font-size: 16.5px;
    color: var(--white);
  }
  .contact-list svg {
    width: 14px;
    height: 14px;
    margin-right: 18px;
    flex: none;
  }
  .back-brand {
    position: absolute;
    left: 318px;
    top: 160px;
    width: 275px;
    margin: 0;
    text-align: center;
    font-weight: 700;
    font-size: 40px;
    letter-spacing: 2px;
    color: var(--white);
  }
  .edge-bar {
    position: absolute;
    right: 0;
    top: 138px;
    width: 9px;
    height: 98px;
    background: var(--red);
  }
  .address {
    position: absolute;
    left: 26px;
    top: 256px;
    margin: 0;
    font-style: normal;
    font-size: 17px;
    line-height: 24px;
    color: var(--soft);
  }
</style>
</head>
<body>
  <section class="card card--front">
    <h1 class="brand-name">VARKO WORKS</h1>
    <div class="front-web">www.varko<span class="accent">works</span>.com</div>
  </section>

  <section class="card card--back">
    <h2 class="holder-name">DANIEL <span class="surname">MARSH</span></h2>

    <div class="contact-band">
      <ul class="contact-list">
        <li>
          <svg viewBox="0 0 16 16" aria-hidden="true"><path fill="#f2f3f6" d="M2 5c0-2 3-3 6-3s6 1 6 3v1h-3V5H5v1H2z M4 7h8l2 6H2z"/></svg>
          (253) 617-4930
        </li>
        <li>
          <svg viewBox="0 0 16 16" aria-hidden="true"><rect x="1" y="3" width="14" height="10" fill="#f2f3f6"/><path d="M1 3l7 6 7-6" fill="none" stroke="#c02026" stroke-width="1.4"/></svg>
          martin@plumlinegroup.com
        </li>
        <li>
          <svg viewBox="0 0 16 16" aria-hidden="true"><g fill="none" stroke="#f2f3f6" stroke-width="1.3"><circle cx="8" cy="8" r="6.5"/><ellipse cx="8" cy="8" rx="3" ry="6.5"/><path d="M1.5 8h13M3 4.5h10M3 11.5h10"/></g></svg>
          www.varkoworks.com
        </li>
      </ul>
    </div>

    <p class="back-brand">VARKO WORKS</p>
    <div class="edge-bar"></div>

    <address class="address">18761 52nd Avenue S,<br>Kent, WA 98047</address>
  </section>
</body>
</html>
```